Construction Company Cellar Crafters needs Business Card

I would like modern looking business card design. I am attaching logo of our company. Please include cell nr 302.418.7650 , email address cellarcrafters4u@examplemail.com, web : cellarcrafters4u.com, please also include wording: Specializing in finishing and remodeling basements. You can play with dark grey and orange colors or any ideas are welcome. Also include social media icons Friendloop and HouseGuidr.

```html
<!DOCTYPE html>
<html lang="en">
<head>
<meta charset="utf-8">
<title>Cellar Crafters – Business Card</title>
<link rel="stylesheet" href="https://fonts.googleapis.com/css2?family=Michroma&family=Open+Sans:wght@400;600;700&display=swap">
<style>
  :root {
    --orange: #f15a29;
    --charcoal: #141414;
    --white: #ffffff;
    --backdrop: #e9e6e2;
    --muted: #bdbdbd;
  }
  * { margin: 0; padding: 0; box-sizing: border-box; }
  html, body {
    width: 1200px; height: 900px; overflow: hidden;
    background: var(--backdrop);
    font-family: "Open Sans", Arial, sans-serif;
  }
  .sheet {
    width: 1200px; height: 900px;
    display: flex; flex-direction: column;
    align-items: center; justify-content: center; gap: 40px;
  }
  .card {
    position: relative;
    width: 680px; height: 389px;
    box-shadow: 0 6px 18px rgba(0,0,0,0.18);
  }
  .card--front { background: var(--orange); color: var(--white); }
  .card--back { background: var(--charcoal); color: var(--white); }

  .brand-name {
    font-family: "Open Sans", Arial, sans-serif;
    font-weight: 700;
    text-transform: uppercase;
    letter-spacing: 2px;
    display: flex; align-items: center; gap: 14px;
  }
  .brand-name .brand-square {
    width: 26px; height: 26px; display: inline-block;
  }
  .card--front .brand-name {
    position: absolute; left: 0; right: 0; top: 130px;
    justify-content: center;
    font-size: 44px; color: var(--white);
  }
  .card--front .brand-square { background: var(--white); }

  .tagline {
    position: absolute; left: 40px; bottom: 36px;
    font-size: 16px; letter-spacing: 1px; font-weight: 400;
    text-transform: uppercase;
  }

  .person { position: absolute; left: 42px; top: 42px; }
  .person-name {
    font-family: "Michroma", Arial, sans-serif;
    color: var(--orange); font-size: 20px; letter-spacing: 1px;
  }
  .person-title { font-size: 15px; margin-top: 4px; font-weight: 600; }

  .card--back .brand-name {
    position: absolute; right: 40px; top: 130px;
    font-size: 34px; color: var(--orange);
  }
  .card--back .brand-square { background: var(--orange); width: 22px; height: 22px; }

  .socials {
    position: absolute; right: 40px; top: 196px;
    display: flex; gap: 18px; font-size: 13px; font-weight: 600;
  }
  .social { display: flex; align-items: center; gap: 6px; color: var(--white); }
  .social-dot { width: 14px; height: 14px; border-radius: 50%; background: var(--muted); }

  .contacts {
    position: absolute; left: 42px; bottom: 38px;
    list-style: none; font-size: 18px; line-height: 30px;
  }
  .contact { display: flex; align-items: center; gap: 10px; }
  .contact svg { width: 14px; height: 14px; flex: none; }
</style>
</head>
<body>
<main class="sheet">
  <section class="card card--front">
    <div class="brand-name"><span class="brand-square"></span>Cellar Crafters</div>
    <p class="tagline">Specializing in finishing and remodeling basements.</p>
  </section>

  <section class="card card--back">
    <div class="person">
      <div class="person-name">MARCUS HALE</div>
      <div class="person-title">Managing Director</div>
    </div>

    <div class="brand-name"><span class="brand-square"></span>Cellar Crafters</div>

    <div class="socials">
      <span class="social"><span class="social-dot"></span>Friendloop</span>
      <span class="social"><span class="social-dot"></span>HouseGuidr</span>
    </div>

    <ul class="contacts">
      <li class="contact">
        <svg viewBox="0 0 16 16" aria-hidden="true"><path fill="#f15a29" d="M3 1l3 3-1.6 1.8a9 9 0 0 0 5.8 5.8L12 10l3 3-2 2C7 15 1 9 1 3z"/></svg>
        302.418.7650
      </li>
      <li class="contact">
        <svg viewBox="0 0 16 16" aria-hidden="true"><rect x="1" y="3" width="14" height="10" fill="#f15a29"/><path d="M1 3l7 6 7-6" fill="none" stroke="#141414" stroke-width="1.4"/></svg>
        cellarcrafters4u@examplemail.com
      </li>
      <li class="contact">
        <svg viewBox="0 0 16 16" aria-hidden="true"><circle cx="8" cy="8" r="6.5" fill="none" stroke="#f15a29" stroke-width="1.6"/><path d="M1.5 8h13M8 1.5c-3 3.5-3 9.5 0 13M8 1.5c3 3.5 3 9.5 0 13" fill="none" stroke="#f15a29" stroke-width="1.2"/></svg>
        cellarcrafters4u.com
      </li>
    </ul>
  </section>
</main>
</body>
</html>
```